Residential & commercial cleaning business

Looking for Brazilian colors, green/blue/yellow.
Name of business is “Marlowe’s Cleaning”.
Second side of card will be for ‘confirming customer next appointment date/time.
Want to include in description…residential & commercial cleaning, experienced, highly recommended, reasonable rates, free estimates, Marlowe’sCleaningCo@brightmop.net, Elmridge, NH, Call today at 555.218.6094.

```html
<!DOCTYPE html>
<html lang="en">
<head>
<meta charset="utf-8">
<title>Marlowe’s Cleaning – Business Card</title>
<link href="https://fonts.googleapis.com/css2?family=Montserrat:wght@400;500;600;700&family=Great+Vibes&display=swap" rel="stylesheet">
<style>
  :root {
    --backdrop: #666666;
    --brand-green: #679a33;
    --brand-yellow: #fbe000;
    --paper: #ffffff;
  }
  html, body {
    margin: 0;
    padding: 0;
    width: 1200px;
    height: 1200px;
    overflow: hidden;
    background: var(--backdrop);
  }
  .card-sheet {
    display: block;
    width: 1200px;
    height: 1200px;
  }
  .sans { font-family: "Montserrat", Arial, sans-serif; }
  .script { font-family: "Great Vibes", cursive; }
  .fill-green { fill: var(--brand-green); }
  .fill-yellow { fill: var(--brand-yellow); }
  .fill-paper { fill: var(--paper); }
  .brand-name { font-weight: 600; font-size: 38px; fill: var(--brand-green); }
  .service-title { font-weight: 500; font-size: 46px; fill: var(--brand-green); }
  .service-list { font-weight: 500; font-size: 18px; fill: var(--brand-green); letter-spacing: 0.5px; }
  .front-contact { font-weight: 500; font-size: 28px; fill: var(--paper); }
  .call-label { font-weight: 700; font-size: 22px; fill: var(--brand-green); }
  .phone-number { font-weight: 700; font-size: 36px; fill: var(--brand-green); letter-spacing: 1px; }
  .appointment-title { font-size: 112px; fill: var(--brand-yellow); }
  .field-pill { fill: var(--brand-yellow); stroke: var(--brand-green); stroke-width: 3; }
  .field-label { font-weight: 500; font-size: 30px; fill: var(--brand-green); }
  .back-contact { font-weight: 500; font-size: 30px; fill: var(--brand-green); }
</style>
</head>
<body>
<svg class="card-sheet" viewBox="0 0 1500 1500" xmlns="http://www.w3.org/2000/svg">
  <defs>
    <clipPath id="front-clip"><rect x="218" y="118" width="1064" height="592"/></clipPath>
    <clipPath id="back-clip"><rect x="218" y="772" width="1064" height="590"/></clipPath>
  </defs>

  <g class="card-front" clip-path="url(#front-clip)">
    <rect class="fill-paper" x="218" y="118" width="1064" height="592"/>
    <path class="fill-yellow" d="M218,505 C330,440 480,420 580,435 C720,455 830,515 905,550 L1165,570 C1250,480 1270,260 1172,118 L1282,118 V710 H218 Z"/>
    <path class="fill-green" d="M218,527 C330,462 480,445 580,458 C720,478 830,535 905,568 L1180,592 C1270,490 1292,260 1218,118 L1282,118 V710 H218 Z"/>

    <g class="brand-lockup">
      <circle class="fill-yellow" cx="336" cy="308" r="14"/>
      <text class="sans brand-name" x="362" y="321">Marlowe’s Cleaning</text>
    </g>

    <g class="services">
      <text class="sans service-title" x="795" y="258">Residential</text>
      <text class="sans service-title" x="795" y="303">&amp; Commercial</text>
      <text class="sans service-title" x="795" y="348">cleaning</text>
      <rect class="fill-yellow" x="800" y="375" width="313" height="3"/>
      <text class="sans service-list" x="802" y="408">EXPERIENCED</text>
      <text class="sans service-list" x="802" y="434">HIGHLY RECOMMENDED</text>
      <text class="sans service-list" x="802" y="460">REASONABLE RATES</text>
      <text class="sans service-list" x="802" y="486">FREE ESTIMATES</text>
    </g>

    <g class="contact">
      <text class="sans front-contact" x="332" y="578">Elmridge, NH</text>
      <text class="sans front-contact" x="332" y="624" textLength="510" lengthAdjust="spacingAndGlyphs">Marlowe’sCleaningCo@brightmop.net</text>
    </g>

    <g class="call-to-action">
      <text class="sans call-label" x="1045" y="548" text-anchor="middle">Call or Text Today (at)</text>
      <rect class="fill-yellow" x="880" y="565" width="318" height="83" rx="41.5"/>
      <text class="sans phone-number" x="1047" y="619" text-anchor="middle">555.218.6094</text>
    </g>
  </g>

  <g class="card-back" clip-path="url(#back-clip)">
    <rect class="fill-green" x="218" y="772" width="1064" height="590"/>
    <path class="fill-yellow" d="M290,1362 C238,1270 236,1090 310,1012 C355,967 440,957 520,975 C640,1005 720,1052 820,1072 C1000,1102 1150,1088 1282,1022 V1362 Z"/>
    <path class="fill-paper" d="M326,1362 C266,1270 263,1110 332,1035 C372,992 442,987 522,1002 C642,1030 722,1077 822,1097 C1002,1127 1152,1112 1282,1048 V1362 Z"/>

    <text class="script appointment-title" x="326" y="925" textLength="872" lengthAdjust="spacingAndGlyphs">Your next Appointment</text>

    <g class="appointment-fields">
      <rect class="field-pill" x="305" y="994" width="414" height="81" rx="40.5"/>
      <text class="sans field-label" x="340" y="1045">Date:</text>
      <rect class="field-pill" x="775" y="994" width="412" height="81" rx="40.5"/>
      <text class="sans field-label" x="814" y="1045">Time:</text>
      <rect class="field-pill" x="305" y="1102" width="884" height="82" rx="41"/>
      <text class="sans field-label" x="340" y="1153">Details:</text>
    </g>

    <g class="contact">
      <text class="sans back-contact" x="748" y="1243" text-anchor="middle">Elmridge, NH</text>
      <text class="sans back-contact" x="748" y="1285" text-anchor="middle">Marlowe’sCleaningCo@brightmop.net</text>
    </g>
  </g>
</svg>
</body>
</html>
```